Design a business card
Business name: Harbourline Growth Advisory
Improving Business Profitibility

- An Overview of the Business & Service:

Business Performance Consulting

- The Target Market: Small to medium-sized business

- Design Specifics:
White card, blue ink, moon eclipse

No Logo

Target Market(s)

Small to medium-sized business

Font styles to use
Sans Serif

```html
<!DOCTYPE html>
<html lang="en">
<head>
<meta charset="utf-8">
<title>Harbourline Growth Advisory – Business Card</title>
<link href="https://fonts.googleapis.com/css2?family=Oswald:wght@400;600&family=Open+Sans:wght@400;600&display=swap" rel="stylesheet">
<style>
  :root {
    --brand-blue: #0a3f93;
    --brand-blue-light: #1550a8;
    --card-white: #e9e9ea;
    --card-white-shade: #dedee0;
    --ink-dark: #2b2b2b;
    --rule-grey: #9a9a9a;
    --backdrop: #4a4a4c;
  }
  * { box-sizing: border-box; margin: 0; padding: 0; }
  html, body { width: 1200px; height: 896px; overflow: hidden; }
  body {
    background: var(--backdrop);
    display: flex; flex-direction: column; align-items: center; justify-content: center;
    gap: 30px;
    font-family: "Open Sans", sans-serif;
  }
  .card {
    width: 720px; height: 411px; position: relative; overflow: hidden;
    box-shadow: 0 8px 24px rgba(0,0,0,0.35);
  }

  /* Front */
  .card-front {
    background: linear-gradient(135deg, var(--brand-blue-light) 0%, var(--brand-blue) 55%);
    color: #fff;
  }
  .front-content { position: absolute; left: 110px; top: 120px; }
  .front-name-main {
    font-family: "Oswald", sans-serif; font-weight: 600; font-size: 48px;
    text-transform: uppercase; line-height: 1.05; letter-spacing: 0.5px;
  }
  .front-name-sub {
    display: block; font-size: 22px; letter-spacing: 9px; margin-top: 4px;
  }
  .front-tagline {
    margin-top: 34px; font-family: "Oswald", sans-serif; font-weight: 400;
    font-size: 19px; text-transform: uppercase; letter-spacing: 1px;
  }

  /* Back */
  .card-back {
    background: linear-gradient(135deg, var(--card-white-shade) 0%, var(--card-white) 50%);
    color: var(--ink-dark);
  }
  .contact-block { position: absolute; left: 56px; top: 70px; }
  .person-name {
    font-family: "Oswald", sans-serif; font-weight: 600; font-size: 28px;
    color: var(--brand-blue); text-transform: uppercase; line-height: 1.1;
  }
  .person-title { font-size: 16px; margin-top: 2px; }
  .contact-rule { width: 290px; height: 1px; background: var(--rule-grey); margin: 12px 0 10px; }
  .contact-list { list-style: none; font-size: 16px; line-height: 1.5; }
  .contact-list li { display: flex; align-items: center; gap: 10px; }
  .contact-list svg { width: 15px; height: 15px; fill: var(--brand-blue); flex: none; }
  .brand-lockup {
    position: absolute; right: 44px; top: 150px; display: flex; align-items: center; gap: 14px;
  }
  .brand-dot { width: 50px; height: 50px; border-radius: 50%; background: var(--brand-blue); flex: none; }
  .brand-name {
    font-family: "Oswald", sans-serif; font-weight: 600; font-size: 27px;
    color: var(--brand-blue); text-transform: uppercase; line-height: 1.05;
  }
  .brand-name-sub { display: block; font-size: 15px; letter-spacing: 7px; margin-top: 2px; }
  .address-block { position: absolute; right: 48px; bottom: 46px; font-size: 17px; line-height: 1.45; }
  .address-rule { width: 260px; height: 1px; background: var(--rule-grey); margin-bottom: 12px; }
</style>
</head>
<body>
  <section class="card card-front">
    <div class="front-content">
      <h1 class="front-name-main">Harbourline Growth<span class="front-name-sub">Advisory</span></h1>
      <p class="front-tagline">Improving Business Profitibility</p>
    </div>
  </section>

  <section class="card card-back">
    <div class="contact-block">
      <h2 class="person-name">Martin Halvorsen</h2>
      <p class="person-title">Managing Director</p>
      <div class="contact-rule"></div>
      <ul class="contact-list">
        <li><svg viewBox="0 0 16 16"><path d="M2 6c0-2 3-4 6-4s6 2 6 4l-3 1-1-2H6L5 7zM3 8h10l1 6H2z"/></svg>044-210 555 018</li>
        <li><svg viewBox="0 0 16 16"><path d="M4 1h8v14H4zM5.5 2.5v9h5v-9z"/></svg>044-210 555 018</li>
        <li><svg viewBox="0 0 16 16"><path d="M1 3h14v10H1zM2 4l6 5 6-5z"/></svg>info@harbourline-advisory.com</li>
        <li><svg viewBox="0 0 16 16"><circle cx="8" cy="8" r="7"/></svg>www.harbourline-advisory.com</li>
      </ul>
    </div>
    <div class="brand-lockup">
      <div class="brand-dot"></div>
      <p class="brand-name">Harbourline Growth<span class="brand-name-sub">Advisory</span></p>
    </div>
    <div class="address-block">
      <div class="address-rule"></div>
      <p>48 Quayside Road,<br>Portmore, 40218</p>
    </div>
  </section>
</body>
</html>
```